military training website velmotrail.com

I have a website that someone designed I am not happy with. It looks like the designer did not have the artistic ability to make a quality product. the power points are ideas that I had for the website. the business proposal was designed by someone else, and I like the style and font used, the website should reflect this document. The main part of the website should be informational with few pictures, maybe some background images behind or off to the side of the text. I would like to include a generic map with four locations marked, which, when you hover the cursor over them, show a picture of the actual location with an artistic effect or blurred so it doesn't look like a plivora atlas snip, and a picture that resembles what services are offered there, along with the text description, pictures can be found in the documents I attached, also can be stock images. this is outlined in the power points roughly.
Want to have the side menu of the major topics, or at the top, and scroll down a single page to find all of the information we have to offer

Target Market(s)

Special operations military

Industry/Entity Type

military

Coding

Coded - Design and coding required

Number of Pages Required

1 page

Other font styles liked:
• Agency FB

Colors
0054AA
0677BA
7BADD7
CADEEF
E8F1F8
00AB8E
00BBA5
67D7C9
C6EFE9
E9F9F6

Requirements
Must have
• interactive "map"
Nice to have
• professional design features to make it look like a professional website, not a beginner designer

```html
<!DOCTYPE html>
<html lang="en">
<head>
<meta charset="utf-8">
<title>Velmo Trail — SOF Training Range</title>
<link rel="stylesheet" href="https://fonts.googleapis.com/css2?family=Audiowide&family=Open+Sans:wght@400;600;700&display=swap">
<style>
:root{
  --navy:#13213f;
  --blue:#4a78b0;
  --band:#5a82b2;
  --blue-deep:#2c5a98;
  --teal:#1fa69a;
  --teal-bright:#00bba5;
  --ink:#333b45;
  --grey:#6b6f74;
  --paper:#f6f7f8;
  --white:#ffffff;
}
*{margin:0;padding:0;box-sizing:border-box}
html,body{width:1200px;height:4234px;overflow:hidden}
body{font-family:"Open Sans",sans-serif;color:var(--ink);background:var(--paper);position:relative}
.display{font-family:"Audiowide",sans-serif;letter-spacing:0;font-weight:400}
section,header,footer{position:absolute;left:0;width:1200px}

/* header */
.site-header{top:0;height:79px;background:var(--navy);z-index:5}
.brand{position:absolute;left:142px;top:-18px;width:200px;height:188px;border-radius:50%;background:var(--navy);border:3px solid #fff;display:flex;align-items:center;justify-content:center;color:#fff;font-weight:700;font-size:20px;z-index:6}
.main-nav a{position:absolute;top:33px;white-space:nowrap;color:#fff;text-decoration:none;font-size:13px;font-weight:700}
.main-nav{position:absolute;left:427px;top:0}
.main-nav a.active{color:#6ea0d8}

/* hero */
.hero{top:0;height:635px}
.hero-photo{position:absolute;inset:0;background:linear-gradient(180deg,#8ea3bc 0%,#a9b7c7 35%,#7e8f86 70%,#6c7b72 100%)}
.hero-title{position:absolute;left:500px;top:196px;color:#fff;font-size:50px;line-height:64px;white-space:nowrap}
.hero-title .boxed{background:var(--blue);padding:0 10px 0 18px;margin-left:-18px}
.hero-lead{position:absolute;left:480px;top:428px;width:545px;color:#fff;font-size:14px;font-weight:600;line-height:22px}
.dot-nav{position:absolute;left:1143px;top:308px;display:flex;flex-direction:column;gap:14px}
.dot-nav span{width:6px;height:6px;border-radius:50%;background:#fff}
.dot-nav span.on{background:var(--teal)}

/* provide */
.provide{top:635px;height:1020px;background:var(--paper)}
.section-title{position:absolute;left:0;width:1200px;text-align:center;color:var(--blue);font-size:43px;line-height:60px}
.section-title .boxed{background:var(--blue);color:#fff;padding:0 10px}
.provide-intro{position:absolute;left:207px;top:165px;width:786px;text-align:center;font-size:13.5px;line-height:22px}
.service{position:absolute;width:420px}
.service h3{font-size:18px;font-weight:600;color:#222;position:relative}
.service h3::before{content:"";position:absolute;left:-34px;top:5px;width:16px;height:16px;border-radius:50%;background:var(--teal)}
.service p{margin-top:14px;width:395px;font-size:12.5px;line-height:21px;color:var(--grey);text-align:justify}
.dot-nav.dim span{background:#c9d3dd}
.dot-nav.dim span.on{background:var(--teal)}

/* mission band */
.mission-band{top:1655px;height:161px;background:var(--band);color:#fff}
.mission-band p{position:absolute;left:158px;top:35px;width:884px;text-align:center;font-size:12.5px;line-height:21px}

/* map */
.map{top:1816px;height:740px;background:var(--paper)}
.map-board{position:absolute;left:145px;top:144px;width:910px;height:517px;background:radial-gradient(ellipse at 50% 50%,#6f8fbf 0%,#3f5f93 45%,#24375d 80%,#1d2b48 100%)}
.marker{position:absolute;width:20px;height:20px;border-radius:50%;background:var(--teal);border:3px solid rgba(255,255,255,.7);cursor:pointer}
.marker:hover{background:var(--teal-bright)}
.map-tip{position:absolute;left:606px;top:92px;width:194px;height:159px;background:#fff;padding:24px 16px;font-size:10.5px;line-height:17.5px;color:#555;box-shadow:0 4px 14px rgba(0,0,0,.3)}

/* qualifications */
.quals{top:2556px;height:607px}
.quals-photo{position:absolute;inset:0;background:linear-gradient(180deg,#f4f3f2 0%,#e9e6e2 30%,#b8a88e 55%,#5c4a33 75%,#3b3123 100%)}
.quals-title{position:absolute;left:141px;top:85px;width:450px;color:var(--blue);font-size:39px;line-height:54px;white-space:nowrap}
.quals-text{position:absolute;left:616px;top:92px;width:441px;font-size:12.5px;line-height:21px;color:var(--grey);text-align:justify}

/* contact */
.contact{top:3163px;height:497px;background:linear-gradient(180deg,#3c6aa8 0%,#2f5c99 55%,#25497f 100%)}
.contact-title{position:absolute;left:0;width:1200px;top:72px;text-align:center;color:#fff;font-size:43px;line-height:60px}
.field{position:absolute;background:#fff;font-size:12.5px;color:#666;padding:0 20px;display:flex;align-items:center}
.field.msg{align-items:flex-start;padding-top:18px}
.submit{position:absolute;left:536px;top:370px;width:128px;height:48px;border-radius:24px;background:var(--teal-bright);color:#fff;font-weight:700;font-size:12.5px;display:flex;align-items:center;justify-content:center}

/* gallery */
.gallery{top:3660px;height:401px;background:#fff}
.shot{position:absolute;top:6px;height:395px}
.arrow{position:absolute;top:193px;width:22px;height:32px;background:#fff;display:flex;align-items:center;justify-content:center}

/* footer */
.site-footer{top:4061px;height:173px;background:var(--paper)}
.footer-brand{position:absolute;left:158px;top:13px;width:138px;height:138px;border-radius:50%;background:var(--navy);border:3px solid #fff;color:#fff;font-weight:700;font-size:15px;display:flex;align-items:center;justify-content:center}
.footer-nav a{position:absolute;top:40px;color:#222;font-size:13px;font-weight:700;text-decoration:none;white-space:nowrap}
.legal{position:absolute;left:376px;top:75px;font-size:11.5px;color:#333}
.social{position:absolute;left:376px;top:110px;display:flex;gap:18px}
.social span{width:12px;height:12px;border-radius:50%;background:#222}
</style>
</head>
<body>

<header class="site-header">
  <div class="brand">Velmo Trail</div>
  <nav class="main-nav">
    <a class="active" style="left:0">MISSION</a>
    <a style="left:96px">WHAT WE PROVIDE</a>
    <a style="left:257px">MAP</a>
    <a style="left:324px">QUALIFICATIONS</a>
    <a style="left:472px">CONTACT</a>
    <a style="left:573px">GALLERY</a>
  </nav>
</header>

<section class="hero" id="mission">
  <div class="hero-photo" role="img" aria-label="Parachutist in free fall high above farmland and a river"></div>
  <h1 class="hero-title display">ATTACK CRANK<br>MASTER THE<br><span class="boxed">MISSION</span></h1>
  <p class="hero-lead">Pioneering realistic training within a strategic theater across the full spectrum of SOF capabilities, liberating warriors from the shackles of logistical burdens and unleashing their full potential to vanquish adversaries</p>
  <div class="dot-nav"><span class="on"></span><span></span><span></span><span></span><span></span><span></span></div>
</section>

<section class="provide" id="provide">
  <h2 class="section-title display" style="top:68px">WHAT WE <span class="boxed">PROVIDE</span></h2>
  <div class="dot-nav dim" style="top:78px"><span></span><span class="on"></span><span></span><span></span><span></span><span></span></div>
  <p class="provide-intro">At Velmo Trail, we draw upon years of invaluable experience gained from training at SOF facilities worldwide. Our journey has culminated in the creation of an all-encompassing training site tailored to meet the exacting needs of SOF operators. We provide a comprehensive range of training modalities meticulously crafted to enhance SOF tactics. Anchored by an unwavering commitment to realism and operational effectiveness, we ensure that your warriors are fully prepared to conquer the most demanding challenges they may face.</p>

  <div class="service" style="left:174px;top:334px"><h3>Precision Marksmanship</h3><p>Utilizing Tier 1 level instructors alongside seasoned local tactical shooting experts, our comprehensive programs incorporate practice with both steel and paper targets, conducted across multiple shooting locations for varied training environments</p></div>
  <div class="service" style="left:661px;top:334px"><h3>Immersive Scenarios</h3><p>We have transformed a former Soviet military stronghold into a dynamic training environment, meticulously furnished with explosives, pyrotechnics, and a live Opposition Force for verisimilar assault scenarios. Underground lays an intricate tunnel system ideal for confined-space rescue and medical training.</p></div>
  <div class="service" style="left:174px;top:516px"><h3>Airfield Dominance</h3><p>With a sprawling 7000ft runway available, we provide an expansive canvas for a myriad of airfield operations, including seizures, static line operations, military free fall, and helicopter insertion and extraction techniques.</p></div>
  <div class="service" style="left:661px;top:516px"><h3>JTAC Support</h3><p>Our team comprises skilled JTACs ready to replicate aircraft in Close Air Support simulations, guaranteeing operators engage in authentic training for air-to-ground coordination, sharpening the skills needed to execute precision strikes with unmatched effectiveness.</p></div>
  <div class="service" style="left:174px;top:698px"><h3>Tactical Vehicles</h3><p>Our designated area enables rigorous vehicular-based training, empowering operators to navigate terrain with confidence and precision</p></div>
  <div class="service" style="left:661px;top:698px"><h3>Comfortable Lodging and Facilities</h3><p>We offer on-site accommodation and mission planning rooms, complete with meticulously prepared meals, as well as sauna and other recreational and fitness amenities. Additionally, transportation services can be readily arranged, ensuring operators are well-rested and fully prepared to engage in rigorous training exercises.</p></div>
  <div class="service" style="left:174px;top:848px"><h3>Cultural Immersion</h3><p>Consider enriching your experience in this captivating region. Allow us to organize a cultural day, including a traditional Estonian sauna and grill experience, a guided tour of historical sites in Tallinn, and an evening filled with vibrant urban nightlife.</p></div>
</section>

<section class="mission-band">
  <p>At Velmo Trail OÜ, our paramount mission is to extend our hospitality to your esteemed team, immersing you in dynamic and authentic training scenarios that cover every aspect of your SOF prowess. We take charge of the logistical challenges, allowing your team to fully concentrate on mastering the mission in Eastern Europe. Our steadfast dedication ensures that every SOF warrior attains the pinnacle of performance and resolute readiness, empowering you to excel in your noble mission: the relentless pursuit of absolute victory with decisive force!</p>
</section>

<section class="map" id="map">
  <h2 class="section-title display" style="top:62px">MAP</h2>
  <div class="map-board" role="img" aria-label="Stylised blue terrain map of the training site with buildings, roads and runway">
    <span class="marker" style="left:577px;top:113px"></span>
    <span class="marker" style="left:351px;top:175px"></span>
    <span class="marker" style="left:304px;top:315px"></span>
    <span class="marker" style="left:647px;top:304px"></span>
    <div class="map-tip">SITE-2<br>7,000FT RUNWAY<br>MFF/SL/HLZ<br>GROUND MOVEMENT TO SITE-2:<br>40MIN<br>HELO MOVEMENT TO SITE-2:<br>5MIN</div>
  </div>
</section>

<section class="quals" id="qualifications">
  <div class="quals-photo" role="img" aria-label="Two operators with radio antennas on a field at sunset"></div>
  <h2 class="quals-title display">QUALIFICATIONS<br>SUMMARY</h2>
  <p class="quals-text">The founders of Velmo Trail OÜ bring forth a wealth of experience and expertise to the table. A former USAF Combat Controller, with nearly a decade of service in Europe; and a highly esteemed former Estonian Special Operator who graduated BUDs and Ranger School, with a proven track record of business success in Estonia. Together, we are steadfast in our dedication to delivering world-class training experiences, deeply rooted in operational excellence and strategic foresight.</p>
</section>

<section class="contact" id="contact">
  <h2 class="contact-title display">CONTACT US</h2>
  <div class="field" style="left:237px;top:163px;width:230px;height:49px">First Name *</div>
  <div class="field" style="left:485px;top:163px;width:230px;height:49px">Last Name *</div>
  <div class="field" style="left:733px;top:163px;width:230px;height:49px">Enter Email *</div>
  <div class="field msg" style="left:237px;top:230px;width:726px;height:120px">Message</div>
  <div class="submit">SUBMIT</div>
</section>

<section class="gallery" id="gallery">
  <div class="shot" style="left:0;width:324px;background:linear-gradient(160deg,#3a3a36,#1d1c1a 60%,#5a4a30)" role="img" aria-label="Operator with night vision beside aircraft at night"></div>
  <div class="shot" style="left:332px;width:536px;background:linear-gradient(180deg,#7b8e5a,#5c7040 60%,#4b5a38)" role="img" aria-label="Helicopter landing on a grassy hill near an operator"></div>
  <div class="shot" style="left:876px;width:324px;background:linear-gradient(180deg,#5a4e44,#8a6a44 55%,#3b3129)" role="img" aria-label="Team boarding a tiltrotor aircraft at dusk"></div>
  <div class="arrow" style="left:0"><svg width="14" height="10" viewBox="0 0 14 10"><path d="M13 5H2M5 1 1 5l4 4" fill="none" stroke="#222" stroke-width="1.6"/></svg></div>
  <div class="arrow" style="left:1178px"><svg width="14" height="10" viewBox="0 0 14 10"><path d="M1 5h11M9 1l4 4-4 4" fill="none" stroke="#222" stroke-width="1.6"/></svg></div>
</section>

<footer class="site-footer">
  <div class="footer-brand">Velmo Trail</div>
  <nav class="footer-nav">
    <a style="left:376px">MISSION</a>
    <a style="left:477px">WHAT WE PROVIDE</a>
    <a style="left:648px">MAP</a>
    <a style="left:720px">QUALIFICATIONS</a>
    <a style="left:877px">CONTACT</a>
    <a style="left:984px">GALLERY</a>
  </nav>
  <p class="legal">© 2024 Velmo Trail.All rights reserved.Privacy &nbsp;|&nbsp; Terms of Use</p>
  <div class="social"><span></span><span></span><span></span><span></span></div>
</footer>

</body>
</html>
```